Modern Attractive Letterhead for Veterinary House Call Business.

A letterhead which can be printed on A4, A5 and A6 paper sizes.
To have: ( our files to be uploaded)
1. Logo with Text
2. telephone
3. email
4. website
5. Address

Target Market(s)

60-85year mainly women pet owners. Also market include families, young professionals, busy people who have dogs and cats

Industry/Entity Type

Business

Requirements
Must have
• 1. Logo with Text ( provided)
• 2. telephone
• 3. email
• 4. website
• 5. Address
Nice to have
• Needs to be modern, preferably warm and caring in nature( if possible )
Should not have
• difficulty in printing A5 and A6

```html
<!DOCTYPE html>
<html lang="en">
<head>
<meta charset="utf-8">
<title>Hearthside Vet Care – Letterhead</title>
<link rel="stylesheet" href="https://fonts.googleapis.com/css2?family=Cinzel:wght@400;600&display=swap">
<style>
  :root {
    --brand-blue: #1f5ea8;
    --brand-green: #3f9c35;
    --ink: #2b2b3a;
    --divider: #b9bcc4;
    --band-light: #2aa8e2;
    --band-dark: #2a2c6b;
    --green-light: #7cc242;
    --green-dark: #17803b;
    --paper: #ffffff;
    --emblem: #e9f0f8;
  }
  * { box-sizing: border-box; margin: 0; padding: 0; }
  html, body { width: 900px; height: 1200px; overflow: hidden; background: var(--paper); }
  .letterhead {
    position: relative;
    width: 900px;
    height: 1200px;
    background: var(--paper);
    font-family: "Cinzel", "Times New Roman", serif;
    color: var(--ink);
  }
  .brand {
    position: absolute;
    left: 60px;
    top: 72px;
    display: flex;
    align-items: center;
    gap: 14px;
  }
  .brand-dot {
    width: 30px;
    height: 30px;
    border-radius: 50%;
    background: var(--brand-blue);
  }
  .brand-name {
    font-size: 34px;
    font-weight: 600;
    color: var(--brand-blue);
    letter-spacing: 0.5px;
  }
  .contact {
    position: absolute;
    left: 606px;
    top: 62px;
    padding-left: 12px;
    border-left: 1px solid var(--divider);
    list-style: none;
    font-size: 14.5px;
    line-height: 21px;
  }
  .contact li { display: flex; align-items: center; gap: 8px; }
  .contact svg { width: 12px; height: 12px; flex: none; }
  .emblem {
    position: absolute;
    left: 290px;
    top: 420px;
    width: 360px;
    height: 360px;
    border-radius: 50%;
    background: radial-gradient(circle at 55% 40%, #f3f7fc 0%, var(--emblem) 70%);
  }
  .footer-wave {
    position: absolute;
    left: 0;
    bottom: 0;
    width: 900px;
    height: 140px;
  }
  .address {
    position: absolute;
    left: 105px;
    width: 260px;
    bottom: 22px;
    text-align: center;
    color: #ffffff;
    font-size: 15.5px;
    line-height: 22px;
    letter-spacing: 0.5px;
  }
</style>
</head>
<body>
<main class="letterhead">
  <header class="brand">
    <span class="brand-dot"></span>
    <span class="brand-name">Hearthside Vet Care</span>
  </header>

  <ul class="contact">
    <li>
      <svg viewBox="0 0 12 12" aria-hidden="true"><path d="M3 1l2 2.3-1.2 1.2a6 6 0 0 0 3.7 3.7L8.7 7 11 9l-1.3 1.8C5.5 10.8 1.2 6.5 1.2 2.3z" fill="none" stroke="var(--brand-green)" stroke-width="1.1"/></svg>
      0400 555 218
    </li>
    <li>
      <svg viewBox="0 0 12 12" aria-hidden="true"><rect x="1" y="3" width="10" height="7" fill="var(--brand-green)"/><path d="M1 3l5 4 5-4" fill="none" stroke="#fff" stroke-width="1"/></svg>
      INFO@HEARTHSIDEVET.COM.AU
    </li>
    <li>
      <svg viewBox="0 0 12 12" aria-hidden="true"><g fill="none" stroke="var(--brand-green)" stroke-width="1"><circle cx="6" cy="6" r="5"/><ellipse cx="6" cy="6" rx="2.2" ry="5"/><path d="M1 6h10"/></g></svg>
      WWW.HEARTHSIDEVET.COM.AU
    </li>
  </ul>

  <div class="emblem" role="img" aria-label="Faint brand emblem placed in the centre of the page"></div>

  <svg class="footer-wave" viewBox="0 0 900 140" preserveAspectRatio="none" aria-hidden="true">
    <defs>
      <linearGradient id="band-blue" x1="0" x2="1" y1="0" y2="0">
        <stop offset="0" stop-color="var(--band-light)"/>
        <stop offset="1" stop-color="var(--band-dark)"/>
      </linearGradient>
      <linearGradient id="band-green" x1="0" x2="1" y1="0" y2="0">
        <stop offset="0" stop-color="var(--green-dark)"/>
        <stop offset="0.45" stop-color="var(--green-light)"/>
        <stop offset="1" stop-color="var(--green-dark)"/>
      </linearGradient>
    </defs>
    <path d="M0,44 C250,20 500,95 655,100 C760,104 850,78 900,60 L900,72 C850,88 760,110 655,106 C500,103 250,52 0,58 Z" fill="url(#band-green)"/>
    <path d="M0,68 C250,52 500,112 655,114 C770,116 850,92 900,80 L900,140 L0,140 Z" fill="url(#band-blue)"/>
  </svg>

  <address class="address">PO Box 482 Ashgrove Vale<br>QLD 4060</address>
</main>
</body>
</html>
```